Supplement Brand Product Labels

Product Label for Supplement Brand

Protein Powder Label (2 x different flavours)

Neon Colours / Skull / Spooky
Refer to pictures below, they are the look we are wanting to go with but put our touch to it aswell.

Target Market(s)

Fitness

Industry/Entity Type

Supplement Brand

Colors
0054AA
0677BA
7BADD7
CADEEF
E8F1F8
0094D4
00A9DD
6FCCEA
C7EBF8
E9F6FB
00AB8E
00BBA5
67D7C9
C6EFE9
E9F9F6
59FF00
82FF00
B8FF75
E3FFCB
F4FFEA
FFF300
FFF600
FEFA6F
FFFEC7
FFFEE8
FFC000
F8CF3A
FAE287
FDF2CF
FEFAEE
F0912C
F2A743
F7CA91
FBE8D2
FDF5EE
EE7325
F08F49
F5BC92
FAE3D3
FDF4ED
EB3D1F
EC4F4E
F09395
F8D3D4
FCEDEE
E54698
E96AAD
F1A4CE
F9D9EA
FCEFF6
A7469A
B969AE
D3A5CF
EDDBEB
F8F0F9
6B429C
8869AF
B7A5CE
E3DAEB
F3F0F8

Requirements
Nice to have
• Skull, Neon Colours, Abstract, Barbell, Lighting Bolt, Flames, Spooky

```html
<!DOCTYPE html>
<html lang="en">
<head>
<meta charset="utf-8">
<title>Protein Powder Label – Back Panel</title>
<link rel="stylesheet" href="https://fonts.googleapis.com/css2?family=Lato:wght@400;700;900&family=Roboto+Slab:wght@800&family=Montserrat:wght@900&display=swap">
<style>
  :root {
    --bg: #000000;
    --ink: #ffffff;
    --panel: #ffffff;
    --panel-ink: #111111;
    --neon: #59FF00;
    --frame: #9a9a9a;
  }
  * { margin: 0; padding: 0; box-sizing: border-box; }
  html, body { width: 883px; height: 1200px; overflow: hidden; background: var(--bg); }
  .label {
    position: relative; width: 883px; height: 1200px; background: var(--bg);
    color: var(--ink); font-family: 'Lato', sans-serif;
  }
  .nutrition {
    position: absolute; left: 27px; top: 57px; width: 512px; height: 411px;
    background: var(--panel); color: var(--panel-ink);
  }
  .nutrition .head {
    position: absolute; top: 11px; font-weight: 700; font-size: 13.2px; line-height: 17px;
  }
  .nutrition .head.serve-info { left: 11px; }
  .nutrition .head.per-serve { left: 215px; width: 160px; text-align: center; }
  .nutrition .head.per-100 { left: 370px; width: 160px; text-align: center; }
  .nutrition .row {
    position: absolute; left: 0; width: 100%; font-size: 15.5px; height: 20px; line-height: 20px;
  }
  .nutrition .row .name { position: absolute; left: 11px; }
  .nutrition .row.sub .name { left: 23px; }
  .nutrition .row .serve { position: absolute; right: 179px; }
  .nutrition .row .hundred { position: absolute; right: 23px; }

  .section-title {
    position: absolute; left: 38px; font-family: 'Roboto Slab', serif; font-weight: 800;
    font-size: 22px; letter-spacing: -0.2px;
  }
  .copy { position: absolute; left: 38px; font-size: 15.5px; line-height: 24.4px; }
  .copy.justified { text-align: justify; text-align-last: left; }

  .amino { position: absolute; left: 608px; top: 60px; width: 240px; }
  .amino h2 {
    font-family: 'Roboto Slab', serif; font-weight: 800; font-size: 21px;
    letter-spacing: -1.1px; white-space: nowrap; text-align: right;
  }
  .amino .cols {
    display: flex; justify-content: space-between; font-weight: 700; font-size: 13.2px;
    margin-top: 17px; line-height: 17px;
  }
  .amino ul { list-style: none; margin-top: 12px; }
  .amino li {
    display: flex; justify-content: space-between; font-size: 15.5px;
    height: 38.65px; line-height: 20px;
  }

  .disclaimer {
    position: absolute; left: 42px; top: 883px; width: 807px; font-size: 15.5px;
    line-height: 24.4px; text-align: justify; text-align-last: left;
  }
  .storage { position: absolute; left: 42px; top: 996px; font-weight: 700; font-size: 15.5px; }

  .origin { position: absolute; left: 50px; top: 1071px; display: flex; align-items: center; gap: 6px; }
  .origin .map { width: 47px; height: 44px; background: var(--neon); border-radius: 10px 14px 16px 8px; }
  .origin .words {
    font-family: 'Montserrat', sans-serif; font-weight: 900; font-size: 21px;
    line-height: 20px; letter-spacing: 0.2px;
  }

  .brand-box {
    position: absolute; left: 585px; top: 979px; width: 260px; height: 189px;
    background: var(--panel); border: 3px solid var(--frame); color: var(--panel-ink);
    text-align: center;
  }
  .brand-box .brand-name {
    margin-top: 48px; font-weight: 900; font-size: 27px; letter-spacing: 0.5px; line-height: 32px;
  }
  .brand-box .web { margin-top: 42px; font-weight: 900; font-size: 17px; letter-spacing: -0.3px; }
  .brand-box .address { margin-top: 6px; font-weight: 900; font-size: 14.5px; letter-spacing: -0.8px; }
</style>
</head>
<body>
<main class="label">

  <section class="nutrition">
    <div class="head serve-info">12.5 Serving Per 1kg Packet<br>80 grams Per Serve</div>
    <div class="head per-serve">Average Quantity<br>Per Serving</div>
    <div class="head per-100">Average Quantity<br>Per 100g</div>
    <div class="row" style="top:73px"><span class="name">Energy (KJ)</span><span class="serve">1286</span><span class="hundred">1608</span></div>
    <div class="row" style="top:121px"><span class="name">Protein (G)</span><span class="serve">24.3</span><span class="hundred">30.4</span></div>
    <div class="row" style="top:170px"><span class="name">Fat, Total (G)</span><span class="serve">1.7</span><span class="hundred">2.1</span></div>
    <div class="row sub" style="top:219px"><span class="name">Saturated (G)</span><span class="serve">1.1</span><span class="hundred">1.3</span></div>
    <div class="row" style="top:268px"><span class="name">Carbohydrates (G)</span><span class="serve">47.6</span><span class="hundred">59.5</span></div>
    <div class="row sub" style="top:316px"><span class="name">Sugar (G)</span><span class="serve">3.5</span><span class="hundred">4.4</span></div>
    <div class="row" style="top:366px"><span class="name">Sodium (MG)</span><span class="serve">68</span><span class="hundred">85</span></div>
  </section>

  <section class="amino">
    <h2>Typical Amino Acid Profile</h2>
    <div class="cols"><span>Amino Acid</span><span>MG/100G</span></div>
    <ul>
      <li><span>Alanine (mg)</span><span>1619</span></li>
      <li><span>Arginine (mg)</span><span>920</span></li>
      <li><span>Aspartic Acid (mg)</span><span>3564</span></li>
      <li><span>Cystine (mg)</span><span>771</span></li>
      <li><span>Glutamic Acid (mg)</span><span>5863</span></li>
      <li><span>Glycine (mg)</span><span>620</span></li>
      <li><span>Histidine (mg)</span><span>628</span></li>
      <li><span>Isoleucine (mg)</span><span>1861</span></li>
      <li><span>Leucine (mg)</span><span>3480</span></li>
      <li><span>Lysine (mg)</span><span>2913</span></li>
      <li><span>Methionine (mg)</span><span>792</span></li>
      <li><span>Phenylalanine (mg)</span><span>1154</span></li>
      <li><span>Proline (mg)</span><span>2400</span></li>
      <li><span>Serine (mg)</span><span>1803</span></li>
      <li><span>Threonine (mg)</span><span>2238</span></li>
      <li><span>Tryptophan (mg)</span><span>529</span></li>
      <li><span>Tyrosine (mg)</span><span>1112</span></li>
      <li><span>Valine (mg)</span><span>1759</span></li>
    </ul>
  </section>

  <h3 class="section-title" style="top:503px">Ingredients</h3>
  <p class="copy" style="top:538px">Maltodextrin, Whey Protein Concentrate, Milk Protein Isolate,<br>Whey Protein Isolate, Branch Chain Amino Acids, Albumin,<br>Wheaten Cornflour, Wholemeal Flour, Cocoa, Flavour, Sucralose.</p>

  <h3 class="section-title" style="top:645px">Allergens</h3>
  <p class="copy" style="top:678px">Egg, Milk, Soy, Wheat, Gluten.</p>

  <h3 class="section-title" style="top:734px">Directions Of Use</h3>
  <p class="copy justified" style="top:767px; width:485px">Mix 2 heaped scoop (40 grams) with 250ml of water or milk and consume immediately. For optimal results, consume 2 – 3 times<br>per day.</p>

  <p class="disclaimer">Formulated supplementary sports food. Not suitable for children under 15 years of age or pregnant women. Should only be used under medical or dietetic supervision. This product is not a sole source of nutrition and should be consumed in conjunction with a nutritious diet and appropriate physical training or exercise program.</p>

  <p class="storage">Store in a cool dry place out of direct sunlight.</p>

  <div class="origin">
    <div class="map" role="img" aria-label="Map of Australia in neon green"></div>
    <div class="words">MADE IN<br>AUSTRALIA</div>
  </div>

  <div class="brand-box">
    <div class="brand-name">VOLTSKULL SUPPS</div>
    <div class="web">www.voltskullsupps.com</div>
    <div class="address">PO BOX 118, Carraway QLD 4510</div>
  </div>

</main>
</body>
</html>
```